New Business Card Design Project

I need a design for business cards, i am an electrical business called "Corvane Electrical and Communications" i need the cards to be double sided with the company logo on the back (attached) the front needs to say my company name, web site, email address, telephone number, and ABN number and electrical license number. I am open to different arrangements of the information but would like the background to be incorporating something electrical or something that looks smart. open to all additional ideas also.

The company colours are orange and grey see logo attached.

Business Name: Corvane Electrical and Communications
Website: corvaneelectricalandcomms.example.com.au
Email: brent@corvaneelectricalandcomms.example.com.au
Telephone(mobile): 0481209736
ABN: 71208349162
Lic No: 418273D

Target Market(s)

Business entities, Project Managers, Accounts, Clients

Industry/Entity Type

Electrician

Contact Information for Business Card

I need a design for business cards, i am an electrical business called "Corvane Electrical and Communications" i need the cards to be double sided with the company logo on the back (attached) the front needs to say my company name

Font styles to use
Serif
Sans Serif

Colors
f37122
5c5c5c

Requirements
Must have
• Must have the Logo on the back open to different ways of it being on the back but had in mind to keep it central but again open to other options
Nice to have
• A real modern cool background that is eye catching yet contemporary
Should not have
• No backgrounds of a light bulb or plug or anything like that

```html
<!DOCTYPE html>
<html lang="en">
<head>
<meta charset="utf-8">
<title>Corvane Electrical and Communications – Business Card</title>
<link rel="stylesheet" href="https://fonts.googleapis.com/css2?family=Exo+2:wght@600;700&family=Roboto+Condensed:ital,wght@0,400;1,400&family=Open+Sans:wght@400&display=swap">
<style>
  :root {
    --page-bg: #3b3b3c;
    --card-grey: #59595b;
    --card-grey-light: #616163;
    --accent-orange: #f7a823;
    --back-orange: #fbae17;
    --text-white: #ffffff;
    --text-soft: #eeeeee;
    --band-white: #ffffff;
    --band-text: #5c5c5c;
    --divider: #8a8a8c;
  }
  * { margin: 0; padding: 0; box-sizing: border-box; }
  html, body {
    width: 1105px; height: 1200px; overflow: hidden;
    background: var(--page-bg);
  }
  .canvas { position: relative; width: 1105px; height: 1200px; }

  .card {
    position: absolute; left: 196px; width: 720px; height: 410px;
    overflow: hidden;
  }

  /* Front */
  .card-front {
    top: 146px;
    background: linear-gradient(180deg, var(--card-grey-light), var(--card-grey));
  }
  .brand-mark {
    position: absolute; left: 41px; top: 150px; width: 250px;
    color: var(--text-white);
    font-family: "Exo 2", sans-serif; font-weight: 600;
    text-align: left;
  }
  .brand-name { font-size: 54px; line-height: 1; letter-spacing: 1px; }
  .brand-tagline { font-size: 12.5px; letter-spacing: 0.6px; margin-top: 8px; text-transform: uppercase; }

  .divider {
    position: absolute; left: 329px; top: 100px; width: 1px; height: 189px;
    background: var(--divider);
  }
  .contact { position: absolute; left: 356px; top: 96px; }
  .person-name {
    font-family: "Exo 2", sans-serif; font-weight: 700;
    font-size: 28px; color: var(--accent-orange); line-height: 1.1;
  }
  .person-title {
    font-family: "Exo 2", sans-serif; font-weight: 700;
    font-size: 19px; color: var(--text-white); margin-top: 2px;
  }
  .detail {
    font-family: "Roboto Condensed", sans-serif;
    font-size: 20px; color: var(--text-soft); line-height: 25px;
  }
  .ids { margin-top: 20px; }
  .contact-lines { margin-top: 10px; }
  .contact-line { display: flex; align-items: center; gap: 8px; }
  .contact-line svg { flex: none; }
  .contact-line.email .detail { font-size: 15.5px; }

  .footer-band { position: absolute; left: 0; top: 0; }
  .front-website {
    position: absolute; left: 0; width: 710px; top: 368px;
    text-align: center;
    font-family: "Roboto Condensed", sans-serif; font-style: italic;
    font-size: 21px; color: var(--band-text);
  }
  .plug-graphic {
    position: absolute; left: 642px; top: 362px; width: 66px; height: 42px;
    background: var(--accent-orange); border-radius: 6px;
  }

  /* Back */
  .card-back {
    top: 602px; background: var(--back-orange);
    display: flex; flex-direction: column; align-items: center;
  }
  .back-brand {
    margin-top: 180px;
    font-family: "Exo 2", sans-serif; font-weight: 600;
    font-size: 60px; color: var(--text-white); line-height: 1;
  }
  .back-website {
    position: absolute; top: 329px; width: 100%; text-align: center;
    font-family: "Open Sans", sans-serif; font-size: 18px;
    letter-spacing: 1.6px; color: var(--text-white);
  }
</style>
</head>
<body>
<main class="canvas">

  <section class="card card-front" aria-label="Business card front">
    <div class="brand-mark">
      <div class="brand-name">Corvane</div>
      <div class="brand-tagline">Electrical &amp; Communications</div>
    </div>

    <div class="divider"></div>

    <div class="contact">
      <div class="person-name">Dale Hartwell</div>
      <div class="person-title">CEO/Founder</div>
      <div class="ids">
        <div class="detail">ABN: 71208349162</div>
        <div class="detail">Lic No: 418273D</div>
      </div>
      <div class="contact-lines">
        <div class="contact-line phone">
          <svg width="11" height="20" viewBox="0 0 11 20" aria-hidden="true">
            <rect x="0.5" y="0.5" width="10" height="19" rx="2" fill="var(--accent-orange)"/>
            <rect x="2" y="3" width="7" height="12" fill="var(--card-grey)"/>
          </svg>
          <span class="detail">0481209736</span>
        </div>
        <div class="contact-line email">
          <svg width="16" height="12" viewBox="0 0 16 12" aria-hidden="true">
            <rect width="16" height="12" rx="1" fill="var(--accent-orange)"/>
            <path d="M1 1 L8 7 L15 1" fill="none" stroke="var(--card-grey)" stroke-width="1.4"/>
          </svg>
          <span class="detail">brent@corvaneelectricalandcomms.example.com.au</span>
        </div>
      </div>
    </div>

    <svg class="footer-band" width="720" height="410" viewBox="0 0 720 410" aria-hidden="true">
      <path d="M0 392 Q330 318 720 372 L720 410 L0 410 Z" fill="var(--band-white)"/>
      <path d="M0 392 Q330 318 720 372" fill="none" stroke="var(--band-text)" stroke-width="3"/>
      <path d="M0 385 Q330 311 720 366" fill="none" stroke="var(--accent-orange)" stroke-width="6"/>
    </svg>
    <div class="front-website">corvaneelectricalandcomms.example.com.au</div>
    <div class="plug-graphic" role="img" aria-label="Orange electrical plug graphic"></div>
  </section>

  <section class="card card-back" aria-label="Business card back">
    <div class="back-brand">Corvane</div>
    <div class="back-website">www.corvaneelectricalandcomms.example.com.au</div>
  </section>

</main>
</body>
</html>
```